Beacon Advisory Website

I currently have a website www.beaconadvisoryinc.com. We are a IT Consulting Company. Our website will pretty much tell out our services. I am looking to enhance my website and make it look more professional. Looking for very classy and Contemporary look and design for my website.

It Company

```html
<!DOCTYPE html>
<html lang="en">
<head>
<meta charset="utf-8">
<title>Beacon Advisory</title>
<link href="https://fonts.googleapis.com/css2?family=Raleway:wght@400;500;600&display=swap" rel="stylesheet">
<style>
:root{
  --navy:#0d4c97;
  --nav-blue:#1a8fd8;
  --nav-dark:#0b4790;
  --card-blue:#1f78cc;
  --card-cyan:#0aa3e0;
  --card-gray:#626262;
  --frame:#c9c9c9;
  --text:#555;
  --footer-bg:#efefef;
  --accent:#0a9ad9;
}
*{margin:0;padding:0;box-sizing:border-box}
html,body{width:1094px;height:1200px;overflow:hidden;background:#fff}
body{font-family:"Raleway",sans-serif;color:var(--text);position:relative}

.site-header{position:absolute;left:0;top:0;width:1094px;height:91px}
.brand{position:absolute;left:69px;top:30px;display:flex;align-items:center;gap:10px}
.brand-mark{width:30px;height:30px;border-radius:50%;background:var(--navy)}
.brand-name{font-size:22px;font-weight:600;color:var(--navy)}

.main-nav{position:absolute;left:381px;top:27px;width:646px;height:44px;
  background:linear-gradient(90deg,#1674c4,var(--nav-blue));
  clip-path:polygon(16px 0,100% 0,calc(100% - 16px) 100%,0 100%)}
.main-nav a{position:absolute;top:0;height:44px;line-height:44px;color:#fff;
  font-size:11px;font-weight:500;text-decoration:none;letter-spacing:.2px}
.main-nav .active{left:0;width:83px;background:var(--nav-dark);text-align:center;padding-left:10px}

.hero{position:absolute;left:0;top:91px;width:1094px;height:551px;
  clip-path:polygon(0 0,100% 0,100% 393px,0 551px);
  background:radial-gradient(circle at 72% 35%,#1aa8e8 0%,#0b4c86 22%,#0a2540 48%,#0a1522 80%)}
.hero-title{position:absolute;left:69px;top:166px}
.hero-title span{display:block;width:max-content;background:rgba(5,15,30,.55);
  color:#fff;font-size:37px;font-weight:600;line-height:44px;padding:0 8px 0 8px;margin-bottom:4px}
.slider-dots{position:absolute;left:68px;top:279px;display:flex;gap:6px}
.slider-dots i{width:10px;height:10px;border-radius:50%;background:#fff}
.slider-dots i.on{background:var(--accent)}

.service{position:absolute;top:449px;width:223px;height:292px;padding:3px;background:var(--frame);
  box-shadow:0 16px 12px -12px rgba(0,0,0,.25)}
.service-inner{height:100%;color:#fff;text-align:center;position:relative}
.service svg{display:block;margin:15px auto 0}
.service h3{font-size:17px;font-weight:500;line-height:20px;margin-top:12px}
.service p{font-size:12.6px;line-height:20px;margin:8px 14px 0}
.service .btn{position:absolute;left:50%;top:235px;transform:translateX(-50%);width:99px;height:32px;
  border:2px solid #fff;color:#fff;font-size:13px;font-weight:500;line-height:28px;text-decoration:none}
.s1{left:335px}.s1 .service-inner{background:var(--card-blue)}
.s2{left:570px}.s2 .service-inner{background:var(--card-cyan)}
.s3{left:804px}.s3 .service-inner{background:linear-gradient(#6e6e6e,#4e4e4e)}

.divider{position:absolute;top:816px;height:1px;background:#ddd}
.welcome{position:absolute;left:68px;top:848px;width:959px;text-align:center}
.welcome h2{font-size:22px;font-weight:500;color:var(--navy)}
.welcome p{font-size:13px;line-height:22px;margin-top:16px;color:#666}
.read-more{position:absolute;left:478px;top:1004px;width:139px;height:37px;background:linear-gradient(#333,#111);
  color:#fff;font-size:13px;font-weight:500;text-align:center;line-height:37px;text-decoration:none}

.site-footer{position:absolute;left:0;top:1075px;width:1094px;height:125px;background:var(--footer-bg);
  border-top:4px solid var(--accent)}
.site-footer .brand{top:19px;left:69px}
.site-footer .brand-mark{width:24px;height:24px}
.site-footer .brand-name{font-size:18px}
.copyright{position:absolute;left:68px;top:76px;font-size:12.5px;color:#444}
.follow{position:absolute;left:864px;top:26px;font-size:12.5px;color:#444}
.social{position:absolute;left:865px;top:50px;display:flex;gap:7px}
.social i{width:27px;height:27px;border-radius:50%}
</style>
</head>
<body>
<header class="site-header">
  <div class="brand"><span class="brand-mark"></span><span class="brand-name">Beacon Advisory</span></div>
  <nav class="main-nav">
    <a class="active" href="#">HOME</a>
    <a href="#" style="left:99px">COMPANY</a>
    <a href="#" style="left:187px">SERVICES</a>
    <a href="#" style="left:274px">SOLUTIONS</a>
    <a href="#" style="left:370px">RESOURCES</a>
    <a href="#" style="left:471px">CAREER</a>
    <a href="#" style="left:547px">CONTACT US</a>
  </nav>
</header>

<section class="hero" role="img" aria-label="Businessman touching glowing blue gears in a technology network">
  <h1 class="hero-title"><span>LOREM IPSUM DOLOR SIT AMET,</span><span>ETUER ADIPISCING ELIT</span></h1>
  <div class="slider-dots"><i class="on"></i><i></i><i></i><i></i></div>
</section>

<article class="service s1"><div class="service-inner">
  <svg width="52" height="48" viewBox="0 0 52 48" fill="#fff"><circle cx="26" cy="6" r="5"/><rect x="20" y="13" width="12" height="16" rx="3"/><rect x="8" y="24" width="36" height="5" rx="2"/><circle cx="6" cy="14" r="4"/><circle cx="46" cy="14" r="4"/><rect x="2" y="20" width="8" height="16" rx="2"/><rect x="42" y="20" width="8" height="16" rx="2"/><rect x="23" y="29" width="6" height="18"/></svg>
  <h3>CONSULTING<br>SERVICES</h3>
  <p>Beacon Advisory has certified professional consultants to work with you to help increase the business by providing IT services ...</p>
  <a class="btn" href="#">Read More</a>
</div></article>

<article class="service s2"><div class="service-inner">
  <svg width="52" height="48" viewBox="0 0 52 48" fill="#fff"><circle cx="26" cy="7" r="6"/><circle cx="14" cy="11" r="4"/><circle cx="38" cy="11" r="4"/><circle cx="5" cy="18" r="4"/><circle cx="47" cy="18" r="4"/><rect x="18" y="15" width="16" height="16" rx="4"/><rect x="0" y="24" width="52" height="10" rx="3"/><circle cx="26" cy="40" r="7"/></svg>
  <h3>STAFF<br>AUGMENTATION</h3>
  <p>For years Beacon Advisory as been offering our customers the ability to augment their existing staff ..</p>
  <a class="btn" href="#">Read More</a>
</div></article>

<article class="service s3"><div class="service-inner">
  <svg width="52" height="48" viewBox="0 0 52 48" fill="#fff"><circle cx="15" cy="32" r="12"/><circle cx="15" cy="32" r="5" fill="#626262"/><path d="M24 20 L40 4 L48 12 L32 28 Z"/><path d="M36 30 l8 8 l-4 4 l-8 -8z"/></svg>
  <h3>OFFSHORE<br>DEVELOPMENT</h3>
  <p>Our Offshore development model has a unique distinction of providing efficient software solutions...</p>
  <a class="btn" href="#">Read More</a>
</div></article>

<div class="divider" style="left:68px;width:450px"></div>
<div class="divider" style="left:577px;width:450px"></div>

<section class="welcome">
  <h2>WELCOME TO BEACON ADVISORY</h2>
  <p>Today's IT market is a dynamic, fast-paced industry, with ever-increasing demands. Meeting these demands for over 25 years, Beacon Advisory maintains a global presence, aggressively recruiting expertly qualified IT and Management Professionals from around the world and cultivating key partnerships with corporations to understand their business models end-to-end, with a goal of delivering exceptional client service and ensuring a consistent delivery of the talent needed to drive results.</p>
</section>
<a class="read-more" href="#">READ MORE</a>

<footer class="site-footer">
  <div class="brand"><span class="brand-mark"></span><span class="brand-name">Beacon Advisory</span></div>
  <p class="copyright">Copyright © 2016. All Right Reserved. Privacy Policy</p>
  <p class="follow">Follow Us:</p>
  <div class="social">
    <i style="background:#2a5aa8"></i><i style="background:#1e9ae0"></i><i style="background:#2a8ccc"></i><i style="background:#444"></i><i style="background:#f58a1f"></i>
  </div>
</footer>
</body>
</html>
```